CBD/HEMP website for e-commerce store

I need a CBD website for my shopify store. I am looking for a layout similar to these site ( https://quietmeadowcbd.com/ ) (https://elmridgecbd.com/) but with my logo and products. I am attaching what my logo looks like so that it helps with the design.

Target Market(s)

CBD HEMP CANNABIS

Industry/Entity Type

Cannabis

Coding

Coded - Design and coding required

Number of Pages Required

5+ page

Requirements
Nice to have
• I would like for it to have a trendy/galaxy feel

```html
<!DOCTYPE html>
<html lang="en">
<head>
<meta charset="utf-8">
<title>Orbitleaf — Home</title>
<link rel="stylesheet" href="https://fonts.googleapis.com/css2?family=Karla:wght@400;700&family=Tinos:wght@400;700&display=swap">
<style>
:root{
  --ink:#1e1a22;
  --muted:#6d6670;
  --pink:#e0357a;
  --blush:#fcf0f5;
  --white:#ffffff;
  --night:#1b0b2e;
  --footer:#170a22;
  --star:#f2b51c;
  --serif:"Tinos", "Times New Roman", serif;
  --sans:"Karla", Arial, sans-serif;
}
*{box-sizing:border-box;margin:0;padding:0}
html,body{width:824px;height:1200px;overflow:hidden;background:var(--white)}
body{font-family:var(--sans);color:var(--ink)}
.page{width:824px;height:1200px;display:flex;flex-direction:column}
.btn{display:inline-block;background:var(--pink);color:var(--white);font:700 8px/1 var(--sans);letter-spacing:.08em;padding:6px 14px;text-transform:uppercase}
.eyebrow{font:700 7px/1 var(--sans);letter-spacing:.12em;text-transform:uppercase}
.section-title{font:400 24px/1.1 var(--serif)}

/* top bar */
.promo{height:14px;background:#2a1240;color:var(--white);font:700 6.5px/14px var(--sans);text-align:center;letter-spacing:.08em}

/* hero */
.hero{position:relative;height:230px;color:var(--white);text-align:center;
  background:linear-gradient(180deg,#241046 0%,#3a1666 40%,#2b1150 74%,#4d6a2a 88%,#5f8a2e 100%)}
.nav{position:absolute;top:14px;left:60px;right:60px;display:flex;align-items:center;justify-content:space-between;font:700 6.5px/1 var(--sans);letter-spacing:.08em}
.nav ul{display:flex;gap:18px;list-style:none}
.brand{display:flex;align-items:center;gap:5px;font:700 20px/1 var(--serif);letter-spacing:.04em}
.brand i{width:10px;height:10px;border-radius:50%;background:var(--pink);display:block}
.hero h1{position:absolute;top:84px;left:0;right:0;font:400 30px/1 var(--serif);letter-spacing:.04em}
.hero h1 span{display:block;font-size:22px;margin-top:6px;letter-spacing:.08em}
.hero .btn{position:absolute;top:164px;left:50%;transform:translateX(-50%)}
.arrow{position:absolute;top:108px;font:400 18px/1 var(--sans);opacity:.8}
.arrow.prev{left:30px}.arrow.next{right:30px}

/* reviews */
.reviews{height:110px;background:var(--blush);padding:14px 60px 0}
.reviews header{display:flex;justify-content:space-between;font:700 8px/1 var(--sans);letter-spacing:.06em}
.review-row{display:grid;grid-template-columns:repeat(4,1fr);gap:16px;margin-top:12px}
.review .meta{font:700 6px/1 var(--sans);color:var(--muted)}
.review .meta b{color:var(--star);letter-spacing:1px;margin-right:4px}
.review h4{font:400 8px/1.4 var(--serif);margin:3px 0}
.review .body{display:flex;gap:6px}
.review .thumb{width:22px;height:22px;flex:none;background:linear-gradient(135deg,#8aa04a,#4f6a23)}
.review p{font:400 5.5px/1.35 var(--sans);color:var(--muted)}
.review .by{font:700 5.5px/1 var(--sans);margin-top:3px}

/* products */
.products{height:230px;text-align:center;padding-top:14px}
.product-grid{display:grid;grid-template-columns:repeat(4,1fr);gap:10px;margin:10px 60px 0;text-align:left}
.product .shot{height:112px;background:radial-gradient(circle at 50% 50%,#9bb25a 0 22%,#f7eef2 48%,#fbf4f7 100%)}
.product .shot.oil{background:radial-gradient(ellipse 14% 36% at 50% 55%,#c6a01c 0 70%,#fbf4f7 100%)}
.product h5{font:400 8px/1 var(--serif);margin-top:6px}
.product small{display:block;font:400 6px/1.5 var(--sans);color:var(--muted)}
.product small b{color:var(--star)}
.products .btn{margin-top:10px}

/* categories */
.categories{height:150px;background:var(--blush);display:grid;grid-template-columns:repeat(3,1fr);gap:4px;padding:8px 8px}
.tile{position:relative;color:var(--white);padding:0 10px 8px;display:flex;flex-direction:column;justify-content:flex-end}
.tile.flowers{background:linear-gradient(180deg,#3c4a33,#1f2a1d)}
.tile.prerolls{background:linear-gradient(180deg,#b9b6b4,#4a2230)}
.tile.vapes{background:linear-gradient(180deg,#8aa15a,#7a5b4a)}
.tile h3{font:400 16px/1 var(--serif);margin:2px 0 5px}
.tile .btn{align-self:flex-start;padding:4px 9px;font-size:6.5px}

/* feature */
.feature{position:relative;height:140px;color:var(--white);text-align:center;
  background:radial-gradient(ellipse at 50% 40%,#2c2f6e 0%,#141a45 55%,#0c1030 100%)}
.feature .ring{position:absolute;left:50%;top:6px;width:128px;height:128px;margin-left:-64px;border-radius:50%;border:1.5px solid rgba(230,220,255,.85);box-shadow:0 0 14px rgba(200,190,255,.6)}
.feature .glow{position:absolute;left:50%;top:20px;width:40px;height:40px;margin-left:-20px;border-radius:50%;background:radial-gradient(circle,#e6a6e0,rgba(180,110,200,0) 70%)}
.feature h2{position:relative;padding-top:58px;font:400 20px/1 var(--serif)}
.feature p{position:relative;width:360px;margin:6px auto 0;font:400 6.5px/1.5 var(--sans)}
.feature .btn{position:relative;margin-top:6px;padding:4px 10px}

/* blog */
.blog{height:200px;background:var(--blush);text-align:center;padding-top:14px}
.post-grid{display:grid;grid-template-columns:repeat(3,1fr);gap:10px;margin:10px 60px 0;text-align:left}
.post .shot{height:66px}
.post .shot.one{background:linear-gradient(135deg,#b7b9a8,#4e5a3a)}
.post .shot.two{background:linear-gradient(135deg,#a66a44,#3c6b2a)}
.post .shot.three{background:linear-gradient(135deg,#2f6f6a,#a57c66)}
.post h4{font:400 8px/1.3 var(--serif);margin-top:5px}
.post p{font:400 5.5px/1.4 var(--sans);color:var(--muted);margin-top:3px}
.post a{display:block;font:700 5.5px/1 var(--sans);color:var(--ink);text-decoration:none;margin-top:4px;letter-spacing:.06em}
.blog .btn{margin-top:10px}

/* footer */
.footer{height:126px;background:var(--footer);color:#e9e2ee;padding:16px 60px 0;position:relative}
.footer-grid{display:grid;grid-template-columns:1.4fr 1fr 1.2fr;gap:24px}
.footer h6{font:700 6.5px/1 var(--sans);letter-spacing:.08em;margin-bottom:6px}
.footer p,.footer li{font:400 6px/1.55 var(--sans);list-style:none}
.footer .contact{margin-top:5px}
.footer .social{display:flex;gap:5px;margin-top:5px}
.footer .social i{width:7px;height:7px;border-radius:50%;background:#e9e2ee;display:block}
.footer .field{margin-top:8px;border:1px solid #e9e2ee;height:16px;font:400 6px/14px var(--sans);padding-left:6px;color:#bfb6c7}
.footer .field + .btn{float:right;margin-top:6px;padding:4px 10px}
.copyright{position:absolute;bottom:8px;left:0;right:0;text-align:center;font:400 6px/1 var(--sans)}
</style>
</head>
<body>
<div class="page">
  <div class="promo">FREE SHIPPING ON ALL ORDERS OVER $99</div>

  <section class="hero" role="img" aria-label="Purple galaxy sky full of stars above a row of cannabis buds">
    <nav class="nav">
      <ul><li>SHOP</li><li>REVIEWS</li><li>BLOG</li><li>OUR STORY</li><li>WHOLESALE</li></ul>
      <div class="brand"><i></i>Orbitleaf</div>
      <ul><li>ACCOUNT</li><li>SEARCH</li><li>CART (0)</li></ul>
    </nav>
    <span class="arrow prev">‹</span><span class="arrow next">›</span>
    <h1>THE ULTIMATE<span>CANNABIS EXPERIENCE</span></h1>
    <a class="btn">Shop now</a>
  </section>

  <section class="reviews">
    <header><span>REAL REVIEWS FROM REAL CUSTOMERS</span><span>‹ ›</span></header>
    <div class="review-row">
      <article class="review"><div class="meta"><b>★★★★★</b>25/12/2020</div><h4>I would definitely recommend this</h4><div class="body"><div class="thumb" role="img" aria-label="Product photo"></div><div><p>Lorem ipsum dolor sit amet, consectetur adipiscing elit, sed do eiusmod tempor incididunt ut labore.</p><div class="by">-John Doe</div></div></div></article>
      <article class="review"><div class="meta"><b>★★★★★</b>25/12/2020</div><h4>I would definitely recommend this</h4><div class="body"><div class="thumb" role="img" aria-label="Product photo"></div><div><p>Lorem ipsum dolor sit amet, consectetur adipiscing elit, sed do eiusmod tempor incididunt ut labore.</p><div class="by">-John Doe</div></div></div></article>
      <article class="review"><div class="meta"><b>★★★★★</b>25/12/2020</div><h4>I would definitely recommend this</h4><div class="body"><div class="thumb" role="img" aria-label="CBD oil bottle photo"></div><div><p>Lorem ipsum dolor sit amet, consectetur adipiscing elit, sed do eiusmod tempor incididunt ut labore.</p><div class="by">-John Doe</div></div></div></article>
      <article class="review"><div class="meta"><b>★★★★★</b>25/12/2020</div><h4>I would definitely recommend this</h4><div class="body"><div class="thumb" role="img" aria-label="Product photo"></div><div><p>Lorem ipsum dolor sit amet, consectetur adipiscing elit, sed do eiusmod tempor incididunt ut labore.</p><div class="by">-John Doe</div></div></div></article>
    </div>
  </section>

  <section class="products">
    <div class="eyebrow">Popular today</div>
    <h2 class="section-title">CBD PRODUCTS</h2>
    <div class="product-grid">
      <div class="product"><div class="shot" role="img" aria-label="CBD flower bud"></div><h5>Product Name</h5><small>Starting at $32</small><small><b>★★★★★</b> 269 Reviews</small></div>
      <div class="product"><div class="shot" role="img" aria-label="Long CBD flower bud"></div><h5>Product Name</h5><small>Starting at $32</small><small><b>★★★★★</b> 269 Reviews</small></div>
      <div class="product"><div class="shot oil" role="img" aria-label="CBD oil dropper bottle"></div><h5>Product Name</h5><small>Starting at $32</small><small><b>★★★★★</b> 269 Reviews</small></div>
      <div class="product"><div class="shot" role="img" aria-label="Small CBD flower buds"></div><h5>Product Name</h5><small>Starting at $32</small><small><b>★★★★★</b> 269 Reviews</small></div>
    </div>
    <a class="btn">Shop now</a>
  </section>

  <section class="categories">
    <div class="tile flowers" role="img" aria-label="Cannabis plant in flower"><span class="eyebrow">CBD</span><h3>Flowers</h3><a class="btn">Shop now</a></div>
    <div class="tile prerolls" role="img" aria-label="Woman smoking a pre-roll"><span class="eyebrow">CBD</span><h3>Pre-Rolls</h3><a class="btn">Shop now</a></div>
    <div class="tile vapes" role="img" aria-label="Woman holding a vape pen outdoors"><span class="eyebrow">CBD</span><h3>Vapes</h3><a class="btn">Shop now</a></div>
  </section>

  <section class="feature" role="img" aria-label="Night sky over a forest with a glowing ring around a cannabis leaf">
    <div class="ring"></div><div class="glow"></div>
    <h2>Beyond the High</h2>
    <p>Lorem ipsum dolor sit amet, consectetur adipiscing elit, sed do eiusmod tempor incididunt ut labore et dolore magna aliqua. Quis ipsum suspendisse ultrices gravida. Risus commodo viverra maecenas accumsan lacus vel facilisis.</p>
    <a class="btn">Shop now</a>
  </section>

  <section class="blog">
    <div class="eyebrow">Blog</div>
    <h2 class="section-title">Shared Secrets</h2>
    <div class="post-grid">
      <article class="post"><div class="shot one" role="img" aria-label="Table with cannabis and rolling supplies"></div><h4>Lorem ipsum dolor sit amctetur adipiscing elit, sed do eiusmod tempor</h4><p>Lorem ipsum dolor sit amet, consectetur adipiscing elit, sed do eiusmod tempor incididunt ut labore et dolore magna aliqua.</p><a>READ MORE →</a></article>
      <article class="post"><div class="shot two" role="img" aria-label="Cookie beside a cannabis leaf"></div><h4>Lorem ipsum dolor sit amctetur adipiscing elit, sed do eiusmod tempor</h4><p>Lorem ipsum dolor sit amet, consectetur adipiscing elit, sed do eiusmod tempor incididunt ut labore et dolore magna aliqua.</p><a>READ MORE →</a></article>
      <article class="post"><div class="shot three" role="img" aria-label="Person lighting a joint"></div><h4>Lorem ipsum dolor sit amctetur adipiscing elit, sed do eiusmod tempor</h4><p>Lorem ipsum dolor sit amet, consectetur adipiscing elit, sed do eiusmod tempor incididunt ut labore et dolore magna aliqua.</p><a>READ MORE →</a></article>
    </div>
    <a class="btn">View all posts</a>
  </section>

  <footer class="footer">
    <div class="footer-grid">
      <div>
        <h6>ABOUT THE SHOP</h6>
        <p>Lorem ipsum dolor sit amet, cocteur adipiscing elit, sed do eiusmod tempor incididunt</p>
        <p style="margin-top:4px">Lorem ipsum dolor sit amet, consecur adipiscing elit, sed do eiusmod tempor incididunt ut labore et dolore magna aliqua.</p>
        <p class="contact">✉ info@orbitleaf.com<br>✆ Call &amp; Text : 888 888 8888</p>
        <div class="social"><i></i><i></i><i></i><i></i></div>
      </div>
      <div>
        <h6>MENU</h6>
        <ul><li>About Us</li><li>Terms &amp; Conditions</li><li>Shipping &amp; Returns</li><li>Privacy Policy</li><li>Disclaimer</li><li>Contact us</li><li>CBD Flower Wholesale</li><li>CBD HEMP F.A.Q</li><li>CBD / Hemp Lab Tests</li></ul>
      </div>
      <div>
        <h6>GET THE DROP</h6>
        <p>Join our newsletter and get updated on new products, strains, and merch.</p>
        <div class="field">Enter your Email address</div>
        <a class="btn">Subscribe</a>
      </div>
    </div>
    <div class="copyright">2020 ORBITLEAF. All Rights Reserved.</div>
  </footer>
</div>
</body>
</html>
```